Insert sheet for our Dog Food Package

We need an information sheet to go inn our pet food package, with branding, and information on ingredients, nutrition and feeding guidance. We will also need two additional items which will be a variation on the label design:
1) Label for package (detailed label about us and our food)
2) Label for outer shipping box (simple label for branding)
We will start with the information, insert page. The winning designer will then deliver the package and box labels as simplified versions of the same graphical theme.
I have attached samples of an earlier drafts of the insert piece. Please disregard the style, form and colors of the examples given. THEY ARE ONLY THERE TO SHOW WHAT INFORMATION SHOULD BE INCLUDED. All colors and style should be from our logo (attached). All graphics, font styles, and placement of elements need to be YOUR creative design - not a copy of the sample we gave. PLEASE READ THIS AND PLEASE DO NOT SUBMIT ANY VARIATION OF THE EXAMPLES!!!!!!!

Target Market(s)

Pet Owners

Industry/Entity Type

Pet Food

Colors
EB3D1F
EC4F4E
F09395
F8D3D4
FCEDEE

Requirements
Must have
• All new design. New colors (based in the palette of our logo), new graphics, new fonts, new placement of elements.
Should not have
• Please disregard the style, form and colors of the examples given. THEY ARE ONLY THERE TO SHOW WHAT INFORMATION SHOULD BE INCLUDED.

```html
<!DOCTYPE html>
<html lang="en">
<head>
<meta charset="utf-8">
<title>Verano Insert Sheet</title>
<link href="https://fonts.googleapis.com/css2?family=Red+Hat+Display:wght@500;700;800&family=Questrial&family=Roboto:wght@400&display=swap" rel="stylesheet">
<style>
  :root {
    --red: #a8231b;
    --paper: #e8e3e1;
    --story-fill: #e3d4d3;
    --ink: #151515;
    --white: #ffffff;
    --stage: #ffffff;
  }
  * { margin: 0; padding: 0; box-sizing: border-box; }
  html, body { width: 1200px; height: 1200px; overflow: hidden; background: var(--stage); }
  .sheet {
    position: absolute; left: 196px; top: 94px; width: 816px; height: 1020px;
    background: var(--paper); font-family: "Questrial", sans-serif; color: var(--ink);
  }
  .band {
    position: absolute; left: 0; top: 47px; width: 100%; height: 138px; background: var(--red); color: var(--white);
  }
  .contact { position: absolute; display: flex; align-items: center; gap: 10px; }
  .contact--phone { left: 36px; top: 50px; }
  .contact--mail { left: 536px; top: 54px; }
  .contact__label { font-family: "Red Hat Display", sans-serif; font-weight: 500; font-size: 14px; letter-spacing: .2px; line-height: 1; }
  .contact__value { font-family: "Red Hat Display", sans-serif; font-weight: 500; line-height: 1.05; }
  .contact--phone .contact__value { font-size: 30px; }
  .contact--mail .contact__value { font-size: 22px; }
  .brand {
    position: absolute; left: 322px; top: 29px; width: 174px; height: 174px; border-radius: 50%;
    background: var(--white); display: flex; align-items: center; justify-content: center;
    font-family: "Red Hat Display", sans-serif; font-weight: 800; font-size: 30px; color: var(--red); letter-spacing: 2px;
  }
  .headline { position: absolute; top: 222px; width: 100%; text-align: center; font-family: "Red Hat Display", sans-serif; }
  .headline__small { font-size: 52px; font-weight: 500; line-height: 1; letter-spacing: 1px; }
  .headline__big { font-size: 70px; font-weight: 800; color: var(--red); line-height: 1.05; letter-spacing: 1px; }
  .motto {
    position: absolute; top: 360px; width: 100%; text-align: center;
    font-family: "Red Hat Display", sans-serif; font-weight: 700; font-size: 26px; line-height: 1.05; padding-left: 30px;
  }
  .motto sup { font-size: 16px; font-weight: 500; }
  .story {
    position: absolute; left: 47px; top: 442px; width: 725px; height: 190px;
    border: 1.5px solid var(--red); border-radius: 25px; background: var(--story-fill); text-align: center;
  }
  .story__title { font-family: "Red Hat Display", sans-serif; font-weight: 800; font-size: 26px; margin-top: 14px; line-height: 1; }
  .accent { color: var(--red); }
  .story__lead { font-size: 17px; line-height: 21px; width: 500px; margin: 8px auto 0; }
  .story__quote { font-size: 15px; line-height: 18px; margin: 4px 18px 0; }
  .section-title {
    position: absolute; top: 672px; width: 100%; text-align: center;
    font-family: "Red Hat Display", sans-serif; font-weight: 800; font-size: 28px; padding-left: 10px;
  }
  .panel {
    position: absolute; top: 722px; width: 279px; height: 262px;
    border: 1.5px solid var(--red); border-radius: 8px; overflow: hidden; background: var(--paper);
  }
  .panel--nutrition { left: 96px; }
  .panel--feeding { left: 449px; }
  .panel__intro { height: 33px; text-align: center; font-size: 17px; line-height: 34px; }
  .panel__bar {
    height: 30px; background: var(--red); color: var(--white); text-align: center;
    font-family: "Red Hat Display", sans-serif; font-weight: 700; font-size: 17px; line-height: 31px; letter-spacing: .3px;
  }
  .nutrients { margin-top: 10px; }
  .nutrients__row {
    display: flex; justify-content: space-between; font-size: 16px; padding: 5px 18px 5px 18px;
    border-bottom: 1px dashed var(--red);
  }
  .ingredients { text-align: center; font-size: 12.5px; line-height: 15.4px; padding: 8px 8px 0; }
  .feeding { width: 100%; border-collapse: collapse; margin-top: 37px; font-family: "Roboto", sans-serif; font-size: 10px; }
  .feeding th { font-weight: 400; text-align: left; padding: 0 12px 4px; border-bottom: 1px dashed var(--red); }
  .feeding td { padding: 5px 12px 4px; }
  .feeding tr.rule td { border-bottom: 1px dashed var(--red); }
  .feeding th:last-child, .feeding td:last-child { padding-left: 0; width: 70px; }
</style>
</head>
<body>
<main class="sheet">
  <header class="band">
    <div class="contact contact--phone">
      <svg width="32" height="32" viewBox="0 0 24 24" aria-hidden="true"><path fill="#fff" d="M6.6 10.8c1.4 2.8 3.8 5.1 6.6 6.6l2.2-2.2c.3-.3.7-.4 1-.2 1.1.4 2.3.6 3.6.6.6 0 1 .4 1 1V20c0 .6-.4 1-1 1C10.6 21 3 13.4 3 4c0-.6.4-1 1-1h3.5c.6 0 1 .4 1 1 0 1.3.2 2.5.6 3.6.1.3 0 .7-.2 1z"/></svg>
      <div>
        <div class="contact__label">FOR MOR INFORMATION</div>
        <div class="contact__value">1-555-010-2040</div>
      </div>
    </div>
    <div class="brand">VERANO</div>
    <div class="contact contact--mail">
      <svg width="34" height="24" viewBox="0 0 34 24" aria-hidden="true"><rect x="1.5" y="1.5" width="31" height="21" fill="none" stroke="#fff" stroke-width="2"/><path d="M1.5 1.5 17 14 32.5 1.5M1.5 22.5 13 11M32.5 22.5 21 11" fill="none" stroke="#fff" stroke-width="2"/></svg>
      <div>
        <div class="contact__label">Email</div>
        <div class="contact__value">hello@veranodog.com</div>
      </div>
    </div>
  </header>

  <h1 class="headline">
    <div class="headline__small">A SUPER</div>
    <div class="headline__big">FOOD REVOLUTION</div>
  </h1>

  <p class="motto"><sup>“</sup>Committed to longer,<br>Healthier lives for dogs<sup>”</sup></p>

  <section class="story">
    <h2 class="story__title">OUR <span class="accent">STORY</span></h2>
    <p class="story__lead">We Revolutionized the indsutry . Not Formulated to meet a minimum standard, but to develop the maximum of the whole dog.</p>
    <p class="story__quote">” we didn’t just set about to create a food that will ‘pass a minimum standard’. We Set out to revolutionize the industry by creating a food that is designed with superfoods, Wholesoe Grains, and Powerful Oils to help your dog achieve their maximum health, happiness and longevity . ’</p>
  </section>

  <h2 class="section-title">PREPARED WITH LOVE <span class="accent">FOR SHADOW</span></h2>

  <section class="panel panel--nutrition">
    <div class="panel__intro">We prepared the best for Shadow</div>
    <div class="panel__bar">NUTRIONAL INFORMATION</div>
    <div class="nutrients">
      <div class="nutrients__row"><span>protein: 15%</span><span>Total Fat 9.5%</span></div>
      <div class="nutrients__row"><span>Crude Fiber: 2.0%</span><span>Moisture: 72%</span></div>
    </div>
    <p class="ingredients">potassium citrate, DiCalcium Phosphate, calcium carbonate, Garbanzo Beans, Choline Bitartrate, Taurine, Salt, Zinc Proteinate, Magnesium Oxide, Iron Proteinate, Vitamin B-12, Selenium, Niazcin, Riboflavin, Calcium Panthothenate, Thiamine, Vitamin A, Vitamin D, Calcium Lodate,</p>
  </section>

  <section class="panel panel--feeding">
    <div class="panel__intro">How much should i feed Shadow?</div>
    <div class="panel__bar">RECOMMENDED FEEDING PLAN</div>
    <table class="feeding">
      <thead><tr><th>APPROXIMATE WEIGHT</th><th>FULL MEAL</th></tr></thead>
      <tbody>
        <tr class="rule"><td>&lt;20 lbs</td><td>110 g</td></tr>
        <tr><td>20-29 lbs</td><td>200 g</td></tr>
        <tr><td>30-39 lbs</td><td>250 g</td></tr>
        <tr class="rule"><td>40-54 lbs</td><td>300 g</td></tr>
        <tr><td>55-69 lbs</td><td>350 g</td></tr>
        <tr class="rule"><td>70-85 lbs</td><td>400 g</td></tr>
        <tr><td>58+ lbs</td><td>500 g</td></tr>
      </tbody>
    </table>
  </section>
</main>
</body>
</html>
```